Business Card Design - Photographer

I am a landscape photographer and I require a business card design. 

I require two designs:
1)  a double sided business card
 and
b)  a single sided business card 

The single sided design can either be the same as the double sided (with just one side having all the information)....or it can be an entire new design. Its up to you.

My corporate colours are (CMYK):

Blue   69, 32, 0, 0
Grey  72,  64,  47,  31
Green  32,  2,  91,  0
Yellow   0, 19, 92, 0
Orange  0, 39, 75, 0

Colour space in final file should be in CMYK.

The details that need to be included on the card:

- Use the provided Logo
- Name: Wiktor Baranowski
- Email:   sales@vistalumeworks.com.au
- Website:    vistalumeworks.com.au
- Twitter:    twitter.com/vistalumeworks
- Facebook:   facebook.com/vistalumeworks
- Mobile  0417 539 662

Please use the attached template to design the logo to the specified size, including the marked bleed lines. I have also attached my logo in PNG (transparent background) and ai format for you to use.

The final file should be:
- Photoshop version with layers so I can edit the name/text etc. All non vector files should be high resolution at 1039 x 697 pixels at 300 dpi.

I also require a file as:
- Vector based PDF

Anyway questions please contact me.

Thank you

Industry/Entity Type

Landscape

Logo styles of interest
Pictorial/Combination Logo
Abstract Logo
Wordmark Logo
Lettermark Logo
Requirements
Must have
• The details that need to be included on the card:

- Use the provided Logo
- Name: Wiktor Baranowski
- Email: sales@vistalumeworks.com.au
- Website: vistalumeworks.com.au
- Twitter: twitter.com/vistalumeworks
- Facebook: facebook.com/vistalumeworks
- Mobile 0417 539 662

```html
<!DOCTYPE html>
<html lang="en">
<head>
<meta charset="utf-8">
<title>Vistalume Works – Business Card</title>
<link rel="stylesheet" href="https://fonts.googleapis.com/css2?family=Cinzel:wght@600&family=Tinos&family=Open+Sans:wght@400&display=swap">
<style>
  :root {
    --ground: #e8e5e0;
    --slate: #3c3f52;
    --paper: #ffffff;
    --sky: #3f8fd2;
    --amber: #f7a43f;
    --ink: #3c3f52;
    --text-light: #ffffff;
  }
  * { margin: 0; padding: 0; box-sizing: border-box; }
  html, body {
    width: 1200px; height: 1047px; overflow: hidden;
    background: var(--ground);
  }
  .canvas { position: relative; width: 1200px; height: 1047px; }

  .card {
    position: absolute;
    width: 757px; height: 432px;
    overflow: hidden;
    box-shadow: 0 2px 6px rgba(0,0,0,0.18);
  }
  .card--front { left: 66px; top: 55px; background: var(--paper); }
  .card--back  { left: 370px; top: 529px; background: var(--slate); }

  .card__waves { position: absolute; inset: 0; width: 100%; height: 100%; }

  .brand {
    position: absolute;
    display: flex; flex-direction: column; align-items: center;
  }
  .brand__dot {
    width: 116px; height: 116px; border-radius: 50%;
    margin-bottom: 44px;
  }
  .brand__name {
    font-family: "Cinzel", "Trajan Pro", serif;
    font-weight: 600;
    font-size: 32px;
    letter-spacing: 1px;
    line-height: 1;
    white-space: nowrap;
  }
  .brand__rule { width: 100%; height: 2px; margin-top: 7px; }

  .card--front .brand { left: 35px; top: 53px; width: 396px; }
  .card--front .brand__dot { background: var(--ink); }
  .card--front .brand__name { color: var(--ink); }
  .card--front .brand__rule { background: var(--ink); }

  .card--back .brand { left: 181px; top: 90px; width: 396px; }
  .card--back .brand__dot { background: var(--text-light); }
  .card--back .brand__name { color: var(--text-light); }
  .card--back .brand__rule { background: var(--text-light); }

  .address {
    position: absolute; right: 23px; top: 62px;
    font-family: "Tinos", "Times New Roman", serif;
    font-size: 18px; line-height: 26px;
    color: var(--ink); text-align: right;
  }

  .contacts {
    position: absolute; right: 23px; top: 290px;
    list-style: none;
    font-family: "Tinos", "Times New Roman", serif;
    font-size: 18px; line-height: 25px;
    color: var(--text-light);
  }
  .contacts__item {
    display: flex; justify-content: flex-end; align-items: center; gap: 6px;
  }
  .contacts__icon { width: 12px; height: 12px; flex: none; }
  .contacts__square { width: 11px; height: 11px; background: var(--sky); border: 1px solid var(--text-light); flex: none; }

  .website {
    position: absolute; left: 0; right: 0; top: 352px;
    text-align: center;
    font-family: "Open Sans", "Helvetica", sans-serif;
    font-size: 19px; letter-spacing: 3px;
    color: var(--text-light);
  }
</style>
</head>
<body>
<main class="canvas">

  <section class="card card--front" aria-label="Business card front">
    <svg class="card__waves" viewBox="0 0 525 300" preserveAspectRatio="none" aria-hidden="true">
      <path fill="var(--slate)" d="M0,288 C140,318 260,250 380,205 C450,180 495,176 525,174 L525,300 L0,300 Z"/>
      <path fill="var(--paper)" d="M0,278 C140,305 255,240 375,198 C445,175 492,170 525,168 L525,174 C495,176 450,180 380,205 C260,250 140,318 0,288 Z"/>
      <path fill="var(--amber)" d="M0,262 C90,282 210,280 335,240 C250,275 140,295 0,282 Z"/>
      <path fill="var(--sky)" d="M85,272 C190,290 300,230 410,190 C465,172 500,166 525,164 L525,171 C498,172 462,180 412,198 C300,240 195,292 85,272 Z"/>
    </svg>

    <div class="brand">
      <div class="brand__dot" aria-hidden="true"></div>
      <span class="brand__name">VISTALUME WORKS</span>
      <div class="brand__rule" aria-hidden="true"></div>
    </div>

    <address class="address">00, Complex Name<br>State Name, City 0020</address>

    <ul class="contacts">
      <li class="contacts__item">
        <svg class="contacts__icon" viewBox="0 0 12 12" aria-hidden="true"><rect x="3" y="0.5" width="6" height="11" rx="1" fill="none" stroke="#fff" stroke-width="1.2"/><rect x="4.3" y="2" width="3.4" height="5" fill="#fff"/></svg>
        <span>0417 539 662</span>
      </li>
      <li class="contacts__item"><span class="contacts__square" aria-hidden="true"></span><span>vistalumeworks</span></li>
      <li class="contacts__item"><span class="contacts__square" aria-hidden="true"></span><span>vistalumeworks</span></li>
      <li class="contacts__item">
        <svg class="contacts__icon" viewBox="0 0 12 12" aria-hidden="true"><rect x="0.5" y="2.5" width="11" height="7" fill="#fff"/><path d="M0.5,2.5 L6,7 L11.5,2.5" fill="none" stroke="#3c3f52" stroke-width="1"/></svg>
        <span>sales@vistalumeworks.com.au</span>
      </li>
      <li class="contacts__item">
        <svg class="contacts__icon" viewBox="0 0 12 12" aria-hidden="true"><circle cx="6" cy="6" r="5.5" fill="#fff"/></svg>
        <span>www.vistalumeworks.com.au</span>
      </li>
    </ul>
  </section>

  <section class="card card--back" aria-label="Business card back">
    <div class="brand">
      <div class="brand__dot" aria-hidden="true"></div>
      <span class="brand__name">VISTALUME WORKS</span>
      <div class="brand__rule" aria-hidden="true"></div>
    </div>
    <p class="website">www.vistalumeworks.com.au</p>
  </section>

</main>
</body>
</html>
```